Demolition Company Billboard Design 13 feet wide 15 feet high

This is my first billboard on a busy road. I want it to be professional but with some eye catching flair that matches by business which is a demoltion business and also list my services. My company slogan is also

"watch kessel clear the lot"

Target Market(s)

Home Ownerd and General Construction Companies

Industry/Entity Type

construction

Colors
0054AA
0677BA
7BADD7
CADEEF
E8F1F8

Requirements
Must have
• My services listed in the pictures my website and my phone number

```html
<!DOCTYPE html>
<html lang="en">
<head>
<meta charset="utf-8">
<title>Kessel Demolition Billboard</title>
<link href="https://fonts.googleapis.com/css2?family=Prata&family=Roboto+Condensed:wght@400;700&display=swap" rel="stylesheet">
<style>
  :root {
    --navy: #0054AA;
    --blue: #0677BA;
    --sky: #7BADD7;
    --mist: #CADEEF;
    --paper: #E8F1F8;
    --ink: #2B2F38;
    --white: #FFFFFF;
    --stage: #D9DEE4;
  }
  * { margin: 0; padding: 0; box-sizing: border-box; }
  html, body { width: 1200px; height: 1200px; overflow: hidden; background: var(--stage); }
  .billboard {
    position: absolute; left: 80px; top: 0;
    width: 1040px; height: 1200px;
    background: linear-gradient(160deg, var(--white) 0%, var(--paper) 100%);
    overflow: hidden;
    font-family: "Roboto Condensed", sans-serif;
  }
  .shapes { position: absolute; inset: 0; }
  .brand {
    position: absolute; left: 60px; top: 96px;
    display: flex; align-items: center; gap: 14px;
    color: var(--white); font-size: 40px; font-weight: 400; letter-spacing: 1px;
  }
  .brand-mark { width: 26px; height: 26px; border: 3px solid var(--white); }
  .hero-visual {
    position: absolute; left: 300px; top: 410px; width: 700px; height: 480px;
    background: linear-gradient(150deg, var(--mist) 0%, var(--sky) 45%, #C9A24A 80%, #8A6A2C 100%);
    border-radius: 6px;
  }
  .slogan {
    position: absolute; right: 30px; top: 245px; text-align: right;
    font-family: "Prata", serif; font-weight: 400; color: var(--navy); line-height: 1.05;
  }
  .slogan-main { display: block; font-size: 76px; }
  .slogan-sub { display: block; font-size: 46px; margin-top: 6px; }
  .services {
    position: absolute; right: 800px; top: 850px; text-align: right;
    list-style: none;
    color: var(--ink); font-size: 42px; line-height: 1.12; text-transform: uppercase;
  }
  .service-dashes { position: absolute; left: 252px; top: 920px; }
  .service-dashes span {
    display: block; width: 74px; height: 11px; background: var(--ink); margin-bottom: 36px;
  }
  .website {
    position: absolute; right: 40px; bottom: 138px;
    color: var(--white); font-size: 36px; font-weight: 400; letter-spacing: 1px;
  }
  .phone {
    position: absolute; right: 40px; bottom: 50px;
    display: flex; align-items: center; gap: 12px;
    color: var(--white); font-size: 60px; font-weight: 700; letter-spacing: 1px;
  }
  .phone svg { width: 40px; height: 60px; }
</style>
</head>
<body>
<main class="billboard">
  <svg class="shapes" viewBox="0 0 1040 1200" width="1040" height="1200" aria-hidden="true">
    <polygon points="0,0 660,0 0,330" fill="var(--navy)"/>
    <polygon points="420,1200 1040,1200 1040,640" fill="var(--blue)"/>
    <rect x="120" y="385" width="130" height="30" fill="var(--sky)"/>
    <rect x="40" y="470" width="210" height="30" fill="var(--sky)"/>
    <rect x="110" y="580" width="140" height="30" fill="var(--sky)"/>
    <rect x="250" y="290" width="28" height="540" fill="var(--navy)"/>
    <rect x="250" y="290" width="130" height="28" fill="var(--navy)"/>
    <rect x="250" y="802" width="50" height="28" fill="var(--navy)"/>
  </svg>

  <div class="brand"><span class="brand-mark"></span>Kessel Demolition</div>

  <div class="hero-visual" role="img" aria-label="Yellow wheel loader with raised bucket in front of light blue city tower illustrations"></div>

  <h1 class="slogan">
    <span class="slogan-main">Watch Kessel</span>
    <span class="slogan-sub">Clear the Lot</span>
  </h1>

  <ul class="services">
    <li>Interior</li>
    <li>Exterior</li>
    <li>Commercial</li>
  </ul>
  <div class="service-dashes" aria-hidden="true"><span></span><span></span></div>

  <div class="website">kesseldemolition.com</div>

  <div class="phone">412-555-0148
    <svg viewBox="0 0 40 60" aria-hidden="true">
      <rect x="4" y="3" width="32" height="54" rx="6" fill="none" stroke="var(--white)" stroke-width="3"/>
      <line x1="15" y1="49" x2="25" y2="49" stroke="var(--white)" stroke-width="3"/>
    </svg>
  </div>
</main>
</body>
</html>
```